Tessaline Wellness Marketing Flyer

We are a new medical practice in the community and need a flyer to send to other medical offices to inform of our services. We just completed our logo with Draftmarketo and would like to incorporate that plus our marketing content into the flyer. Our medical practice has 2 divisions: (1)Mental Health/Psychiatry and (2) Migraine and Neurospasticity Management. Please see website for content and provider photos at www.TessaWellnet.com

Target Market(s)

Other Healthcare Professionals in the Community

Industry/Entity Type

Medical

Requirements
Must have
• Photos of all 5 healthcare providers, phone number, address, logo

```html
<!DOCTYPE html>
<html lang="en">
<head>
<meta charset="utf-8">
<title>Tessaline Wellness Flyer</title>
<link rel="stylesheet" href="https://fonts.googleapis.com/css2?family=Montserrat:wght@400;500;600;700&display=swap">
<style>
  :root {
    --backdrop: #1b1b1b;
    --paper: #ffffff;
    --teal: #2bb3a7;
    --teal-deep: #1a9a87;
    --teal-light: #47c2b7;
    --green: #a8d15a;
    --ink: #333333;
    --pill: #3d3d3d;
    --mist: #e8e9ea;
    --blob: #dcefef;
  }
  * { box-sizing: border-box; margin: 0; padding: 0; }
  html, body { width: 1200px; height: 1200px; overflow: hidden; background: var(--backdrop); }
  body { font-family: "Montserrat", sans-serif; color: var(--ink); position: relative; }

  .flyer { position: absolute; left: 209px; top: 52px; width: 782px; height: 1097px; background: var(--paper); overflow: hidden; }
  .hero-art { position: absolute; left: 0; top: 0; }

  .brand { position: absolute; left: 26px; top: 26px; width: 240px; text-align: center; }
  .brand-dot { width: 62px; height: 62px; border-radius: 50%; background: var(--teal); margin: 0 auto 14px; }
  .brand-name { font-size: 26px; font-weight: 600; color: var(--teal); line-height: 1.15; }

  .headline { position: absolute; left: 26px; top: 182px; font-size: 37px; font-weight: 700; color: var(--teal); line-height: 43px; }
  .intro { position: absolute; left: 25px; top: 331px; font-size: 15px; }

  .division { position: absolute; text-align: center; }
  .division--mental { left: 26px; top: 368px; width: 294px; }
  .division--migraine { left: 375px; top: 360px; width: 384px; }
  .division-figure { margin: 0 auto; background: var(--blob); border-radius: 46% 54% 48% 52% / 55% 50% 50% 45%; }
  .division--mental .division-figure { width: 84px; height: 64px; margin-top: 4px; }
  .division--migraine .division-figure { width: 84px; height: 74px; }
  .division-title { font-size: 17.5px; font-weight: 600; color: var(--teal); line-height: 23px; margin-top: 14px; }
  .division-text { font-size: 13.8px; line-height: 20.5px; margin-top: 10px; }
  .division-line { display: block; white-space: nowrap; text-align: justify; text-align-last: justify; }
  .division-line--end { text-align-last: center; }
  .division-line--tight { letter-spacing: -0.25px; }
  .divider { position: absolute; left: 347px; top: 455px; width: 2px; height: 167px; background: var(--green); }

  .providers-tag { position: absolute; left: 277px; top: 644px; width: 228px; height: 29px; border-radius: 15px; background: var(--green); box-shadow: 2px 2px 0 var(--pill); font-size: 20px; font-weight: 700; text-align: center; line-height: 29px; }
  .providers { position: absolute; left: 0; top: 680px; width: 782px; height: 192px; background: var(--green); }
  .provider { position: absolute; top: 16px; width: 150px; margin-left: -75px; text-align: center; }
  .provider-photo { width: 130px; height: 130px; margin: 0 auto; border-radius: 50%; border: 4px solid #fff; box-shadow: 0 3px 6px rgba(0,0,0,.25); }
  .provider-name { display: inline-block; margin-top: 12px; padding: 2px 9px; border-radius: 8px; background: var(--pill); color: #fff; font-size: 14.5px; font-weight: 500; white-space: nowrap; }

  .values { position: absolute; left: 0; top: 872px; width: 782px; height: 115px; background: var(--mist); display: flex; }
  .value { text-align: center; padding-top: 12px; }
  .value + .value { border-left: 2px solid #fff; }
  .value-label { font-size: 18.5px; font-weight: 700; color: var(--teal); margin-top: 8px; }

  .contact { position: absolute; left: 0; top: 987px; width: 782px; height: 110px; background: linear-gradient(180deg, var(--teal-deep), var(--teal-light)); color: #fff; font-size: 13.7px; }
  .contact-tag { position: absolute; left: 310px; top: 8px; width: 168px; height: 29px; border-radius: 15px; background: #fff; box-shadow: 2px 2px 0 var(--pill); color: var(--ink); font-size: 20px; font-weight: 700; text-align: center; line-height: 29px; }
  .contact-item { position: absolute; display: flex; align-items: center; gap: 7px; white-space: nowrap; }
  .contact-icon { width: 14px; height: 14px; border: 1.2px solid #fff; border-radius: 50%; display: flex; align-items: center; justify-content: center; }
  .social-rule { position: absolute; left: 633px; top: 44px; width: 2px; height: 17px; background: #fff; }
  .social-dot { width: 14px; height: 14px; border: 1.2px solid #fff; border-radius: 50%; }
</style>
</head>
<body>
<main class="flyer">
  <svg class="hero-art" width="782" height="420" viewBox="0 0 782 420">
    <defs>
      <radialGradient id="family-tones" cx="50%" cy="45%" r="60%">
        <stop offset="0" stop-color="#b77a4e"/>
        <stop offset=".55" stop-color="#6e5a3c"/>
        <stop offset="1" stop-color="#8f7b55"/>
      </radialGradient>
      <clipPath id="hero-clip"><rect width="782" height="420"/></clipPath>
    </defs>
    <g clip-path="url(#hero-clip)">
      <path d="M305 0 C365 0 372 100 380 170 C395 300 540 410 782 330 L782 0 Z" fill="var(--green)"/>
      <circle cx="596" cy="140" r="212" fill="url(#family-tones)" role="img" aria-label="Photo of a smiling family outdoors with pumpkins at an autumn farm"/>
    </g>
  </svg>

  <div class="brand">
    <div class="brand-dot"></div>
    <div class="brand-name">Tessaline Wellness</div>
  </div>

  <h1 class="headline">Helping Bodies<br>Helping Minds<br>Helping You</h1>
  <p class="intro">Our medical practice has 2 divisions:</p>

  <section class="division division--mental">
    <div class="division-figure" role="img" aria-label="Stethoscope illustration on a pale teal shape"></div>
    <h2 class="division-title">Mental Health/Psychiatry</h2>
    <p class="division-text">
      <span class="division-line">Bringing comprehensive evaluation,</span>
      <span class="division-line">medication management and psycho-</span>
      <span class="division-line">therapy to the full spectrum of mental</span>
      <span class="division-line division-line--tight">health disorders including minor, moder-</span>
      <span class="division-line division-line--tight">ate and major depression, bipolar disor-</span>
      <span class="division-line division-line--tight">der, ADD/ADHD, anxiety, schizophrenia,</span>
      <span class="division-line division-line--end">stress or grief reactions, and others</span>
    </p>
  </section>

  <div class="divider"></div>

  <section class="division division--migraine">
    <div class="division-figure" role="img" aria-label="Dandelion illustration on a pale teal shape"></div>
    <h2 class="division-title">Migraine and Neurospasticity<br>Management</h2>
    <p class="division-text">
      <span class="division-line">Injections of botulinum neurotoxin are a widely used</span>
      <span class="division-line">therapeutic form of treatment for both chronic</span>
      <span class="division-line">migraines and patients with involuntary muscle con-</span>
      <span class="division-line division-line--tight">tractions (neurospasticity). Injections may offer up to 3</span>
      <span class="division-line">months of relief and may be combined with other</span>
      <span class="division-line division-line--end">pharmaceutical interventions for maximum benefit</span>
    </p>
  </section>

  <div class="providers-tag">Meet Our Providers</div>

  <section class="providers">
    <div class="provider" style="left:94px"><div class="provider-photo" role="img" aria-label="Headshot of Aron Velik" style="background:radial-gradient(#c9a593,#5f6b70)"></div><span class="provider-name">Aron Velik</span></div>
    <div class="provider" style="left:243px"><div class="provider-photo" role="img" aria-label="Headshot of Maris Caldwell" style="background:radial-gradient(#c79a84,#5b4f49)"></div><span class="provider-name">Maris Caldwell</span></div>
    <div class="provider" style="left:391px"><div class="provider-photo" role="img" aria-label="Headshot of Dane Orrick" style="background:radial-gradient(#c8a192,#4f5a60)"></div><span class="provider-name">Dane Orrick</span></div>
    <div class="provider" style="left:540px"><div class="provider-photo" role="img" aria-label="Headshot of Lorna Vettig" style="background:radial-gradient(#d4b4a6,#6a7a80)"></div><span class="provider-name">Lorna Vettig</span></div>
    <div class="provider" style="left:689px"><div class="provider-photo" role="img" aria-label="Headshot of Dr. Cyril Ambrose" style="background:radial-gradient(#d1a98d,#7a5638)"></div><span class="provider-name">Dr. Cyril Ambrose</span></div>
  </section>

  <section class="values">
    <div class="value" style="width:277px">
      <svg width="44" height="56" viewBox="0 0 44 56">
        <path d="M10 32 L4 50 L12 46 L16 54 L20 38 Z M34 32 L40 50 L32 46 L28 54 L24 38 Z" fill="var(--pill)"/>
        <circle cx="22" cy="20" r="19" fill="var(--pill)"/>
        <circle cx="22" cy="20" r="12" fill="none" stroke="#fff" stroke-width="2"/>
        <path d="M16 20 L21 25 L29 15" fill="none" stroke="#fff" stroke-width="2.5"/>
      </svg>
      <div class="value-label">Board Certified</div>
    </div>
    <div class="value" style="width:232px">
      <svg width="52" height="56" viewBox="0 0 52 56">
        <path d="M26 10 C40 10 50 18 50 30 C50 42 40 48 26 48 C22 48 18 47 15 46 L4 54 L8 43 C4 39 2 35 2 30 C2 18 12 10 26 10 Z" fill="var(--pill)"/>
        <path d="M18 12 L24 2 L28 12 Z" fill="var(--pill)"/>
        <g fill="#fff"><circle cx="16" cy="32" r="1.3"/><circle cx="21" cy="32" r="1.3"/><circle cx="26" cy="32" r="1.3"/><circle cx="31" cy="32" r="1.3"/><circle cx="36" cy="32" r="1.3"/></g>
      </svg>
      <div class="value-label">Responsive</div>
    </div>
    <div class="value" style="width:273px">
      <svg width="56" height="56" viewBox="0 0 56 56">
        <path d="M28 52 L6 30 C-2 22 2 6 14 4 C20 3 25 6 28 10 C31 6 36 3 42 4 C54 6 58 22 50 30 Z" fill="var(--pill)"/>
        <path d="M14 28 L26 18 L34 24 M22 36 L32 28 M28 42 L36 34" fill="none" stroke="#fff" stroke-width="2.2"/>
      </svg>
      <div class="value-label">Compassionate</div>
    </div>
  </section>

  <footer class="contact">
    <div class="contact-tag">Let’s Connect</div>
    <div class="contact-item" style="left:24px;top:45px">
      <span class="contact-icon"><svg width="8" height="8" viewBox="0 0 8 8"><path d="M1 1 L3 1 L3.5 3 L2.5 3.6 C3 4.8 3.6 5.4 4.6 5.6 L5 4.6 L7 5 L7 7 C3.5 7 1 4.5 1 1 Z" fill="#fff"/></svg></span>208-555-0147
    </div>
    <div class="contact-item" style="left:24px;top:68px">
      <span class="contact-icon"><svg width="9" height="9" viewBox="0 0 10 10"><circle cx="5" cy="5" r="4" fill="none" stroke="#fff"/><path d="M1 5 H9 M5 1 V9" stroke="#fff" stroke-width=".8"/></svg></span>www.TessaWellnet.com
    </div>
    <div class="contact-item" style="left:291px;top:45px">
      <span class="contact-icon"><svg width="8" height="6" viewBox="0 0 8 6"><rect x=".5" y=".5" width="7" height="5" fill="none" stroke="#fff"/><path d="M.5 .5 L4 3.5 L7.5 .5" fill="none" stroke="#fff"/></svg></span>support@TessaWellnet.com
    </div>
    <div class="contact-item" style="left:291px;top:68px">
      <span class="contact-icon"><svg width="7" height="9" viewBox="0 0 7 9"><path d="M3.5 9 C1 6 0 4.5 0 3.5 A3.5 3.5 0 0 1 7 3.5 C7 4.5 6 6 3.5 9 Z" fill="#fff"/><circle cx="3.5" cy="3.5" r="1.2" fill="var(--teal-deep)"/></svg></span>415 N. Larchmont Ave, Suite B, Coeur d'Alene, ID&nbsp; 83814
    </div>
    <div class="social-rule"></div>
    <div class="contact-item" style="left:650px;top:45px">Social Media: <span class="social-dot"></span></div>
  </footer>
</main>
</body>
</html>
```